Bramblewood Joinery Website

My client Bramblewood Joinery is looking for a redesign for a Word Press Website. Their current site is at www.bramblewoodjoinery.example They are a custom cabinet company, but also create bathroom, living room, bar and entertainment and bedroom cabinets too. They would like a design that emulates the master craftsman work they do yet a contemporary style.

Their current site was designed using Flash elements.

Target Market(s)

Home owners and builders of high end homes

Industry/Entity Type

Entertainment

Font styles to use
Serif
Decorative

Requirements
Must have
• Must show their work and logo using a contemporary style.
Nice to have
• Sliders that showcase their projects.

```html
<!DOCTYPE html>
<html lang="en">
<head>
<meta charset="utf-8">
<title>Bramblewood Joinery</title>
<link href="https://fonts.googleapis.com/css2?family=Oswald:wght@500;700&family=Open+Sans:wght@400;600;700&family=Cabin:wght@400;500&display=swap" rel="stylesheet">
<style>
:root{
  --green:#3aac3a;
  --green-dark:#2a8a2a;
  --wood:#7a3f1f;
  --wood-dark:#4d2410;
  --wood-light:#9b5a2e;
  --oak:#b79a74;
  --ink:#222;
  --muted:#666;
  --grey:#dcdcdc;
  --black:#141414;
  --navy:#1f2433;
}
*{margin:0;padding:0;box-sizing:border-box}
html,body{width:1200px;height:2419px;overflow:hidden}
body{position:relative;background:#fff;font-family:'Open Sans',sans-serif;color:var(--ink)}
.abs{position:absolute}
.header{left:0;top:0;width:1200px;height:126px;background:#fff;border-top:3px solid var(--green)}
.brand{left:168px;top:18px;display:flex;align-items:center;gap:12px}
.brand-mark{width:92px;height:92px;border-radius:50%;border:4px solid var(--green)}
.brand-name{font-family:'Open Sans',sans-serif;font-weight:700;font-size:22px;color:var(--green)}
.search{left:815px;top:19px;width:222px;height:32px;border:1px solid #ccc;display:flex}
.search span{flex:1;font-size:13px;color:#999;padding:7px 10px}
.search i{width:32px;background:var(--wood);display:block}
.social-badge{left:735px;top:64px;width:140px;height:44px;border:1px solid #bbb;background:#f4f4f4;display:flex;align-items:center;gap:8px;padding-left:8px}
.social-badge b{width:26px;height:26px;background:var(--navy);display:block}
.social-badge span{font-size:13px;color:var(--navy);font-weight:600;line-height:1.1}
.call{left:890px;top:64px;text-align:left}
.call small{display:block;font-size:12px;color:#333}
.call strong{font-family:'Oswald',sans-serif;font-size:30px;color:var(--green);font-weight:700;line-height:1.1}
.nav-band{left:0;top:126px;width:1200px;height:72px;background:var(--black)}
.nav{left:160px;top:138px;width:880px;height:55px;background:linear-gradient(#8a4a22,#6b3618);display:flex;align-items:center}
.nav .home{width:46px;height:40px;background:var(--black);margin:0 10px 0 8px;display:flex;align-items:center;justify-content:center}
.nav a{color:#f2e6d8;font-size:12.5px;font-weight:600;text-decoration:none;margin:0 12px;letter-spacing:.3px}
.hero-band{left:0;top:198px;width:1200px;height:340px;background:linear-gradient(90deg,#a88a64,#c3a783 50%,#a88a64)}
.hero{left:160px;top:225px;width:880px;height:375px;background:linear-gradient(160deg,#6b3a1a,#a5622c 45%,#4a2a14);border-radius:3px}
.hero h1{left:0;width:880px;top:228px;text-align:center;font-family:'Oswald',sans-serif;font-weight:700;font-size:40px;color:#fff;letter-spacing:.5px}
.hero p{left:0;width:880px;top:284px;text-align:center;font-size:18px;color:#fff}
.dots{left:390px;top:330px;display:flex;gap:6px;background:rgba(0,0,0,.3);padding:4px 6px;border-radius:10px}
.dots i{width:13px;height:13px;border-radius:50%;background:#ddd;display:block}
.dots i:first-child{background:var(--green)}
.arrow{top:160px;width:48px;height:48px;border-radius:50%;background:rgba(255,255,255,.3)}
.tagline{left:0;top:633px;width:1200px;text-align:center;font-size:28px;line-height:36px;color:#333}
.tagline em{font-style:normal;color:var(--green)}
.offer{left:0;top:750px;width:1200px;height:416px;background:linear-gradient(90deg,var(--wood-dark),var(--wood-light) 30%,#8d4c24 60%,var(--wood-dark));border-top:3px solid #5a1010;border-bottom:3px solid #5a1010}
.offer-tab{left:440px;top:-3px;width:330px;height:46px;background:var(--green);clip-path:polygon(0 0,100% 0,94% 100%,6% 100%);color:#fff;font-family:'Cabin',sans-serif;font-size:20px;text-align:center;line-height:44px;letter-spacing:1px}
.service{top:88px;width:150px;text-align:center}
.service .ring{width:116px;height:116px;margin:0 auto;border-radius:50%;background:var(--green);border:4px solid #fff;display:flex;align-items:center;justify-content:center}
.service.active .ring{background:#222}
.service span{display:block;margin-top:10px;color:#fff;font-size:13px;font-weight:600}
.offer p{left:165px;top:278px;width:870px;text-align:center;color:#f0e4d6;font-size:13.5px;line-height:24px}
h2.sec{font-family:'Cabin',sans-serif;font-weight:400;font-size:22px;color:#222;letter-spacing:.5px}
.thumb{width:193px;height:102px;background:linear-gradient(135deg,#cfc6b8,#5d4a3a)}
.btn{height:32px;line-height:32px;text-align:center;font-size:12px;color:#fff}
.news-item{left:786px;width:254px;display:flex;gap:8px}
.news-item .pic{width:54px;height:46px;background:linear-gradient(135deg,#b9a58c,#4d3a2c);flex:none}
.news-item b{display:block;font-size:12.5px;color:var(--green);font-weight:400}
.news-item span{font-size:11.5px;color:#555;line-height:16px}
.rule{left:160px;top:1568px;width:880px;height:1px;background:#ddd}
.client{font-family:'Oswald',sans-serif;font-size:34px;color:#111;font-weight:500}
.quote{left:718px;top:1652px;width:322px;height:186px;background:var(--green);border:3px solid #dfe;padding:12px 16px;color:#fff;font-style:italic;font-size:12.5px;line-height:18px;text-align:center;border-radius:2px}
.hello{left:0;top:1843px;width:1200px;height:202px;background:var(--grey)}
.hello h3{left:0;width:1200px;top:55px;text-align:center;font-family:'Oswald',sans-serif;font-size:36px;font-weight:700;color:#222}
.hello p{left:160px;width:880px;top:112px;text-align:center;font-size:13px;color:#666;line-height:20px}
.circle{width:40px;height:40px;border-radius:50%}
.footer{left:0;top:2045px;width:1200px;height:338px;background:linear-gradient(90deg,var(--wood-dark),var(--wood-light) 35%,#8a4822 70%,var(--wood-dark));border-top:4px solid #5a1010}
.footer h4{font-family:'Cabin',sans-serif;font-weight:500;font-size:16px;color:#fff;letter-spacing:.5px}
.footer p{font-size:12.5px;line-height:21px;color:#f3e8dc}
.fthumb{width:53px;height:48px;background:linear-gradient(135deg,#c9bba6,#4c3828)}
.bottom{left:0;top:2383px;width:1200px;height:36px;background:#2a1208;color:#f0e0d0;font-size:12px}
</style>
</head>
<body>

<header class="abs header">
  <div class="abs brand"><div class="brand-mark"></div><span class="brand-name">Bramblewood Joinery</span></div>
  <div class="abs search"><span>enter keyword...</span><i></i></div>
  <div class="abs social-badge"><b></b><span>Find us on<br>Social</span></div>
  <div class="abs call"><small>Have a Question for Us?</small><strong>555 014 2288</strong></div>
</header>

<div class="abs nav-band"></div>
<nav class="abs nav">
  <div class="home"><svg width="22" height="20" viewBox="0 0 22 20"><path d="M11 1L1 10h3v9h5v-6h4v6h5v-9h3z" fill="#fff"/></svg></div>
  <a>WHO WE ARE</a><a>GETTING STARTED</a><a>CONTACT US</a><a>CUSTOMER EXPERIENCE</a><a>PROFESSIONAL</a><a>PORTFOLIO</a><a>CABINET HARDWARE</a>
</nav>

<div class="abs hero-band"></div>
<section class="abs hero" role="img" aria-label="Photo of a finished wooden kitchen with central island">
  <div class="abs arrow" style="left:12px"><svg width="48" height="48"><path d="M28 14l-10 10 10 10" stroke="#fff" stroke-width="4" fill="none"/></svg></div>
  <div class="abs arrow" style="right:12px"><svg width="48" height="48"><path d="M20 14l10 10-10 10" stroke="#fff" stroke-width="4" fill="none"/></svg></div>
  <h1 class="abs">AFFORDABLE SOLUTIONS FOR LIVING</h1>
  <p class="abs">Style, Comfort, Quality, Selection!</p>
  <div class="abs dots"><i></i><i></i><i></i><i></i><i></i></div>
</section>

<p class="abs tagline">We've been <em>designing and manufacturing</em><br>the Midwest's finest <em>custom cabinets and fixtures</em> since <em>1966</em></p>

<section class="abs offer">
  <div class="abs offer-tab">WHAT WE OFFER</div>
  <div class="abs service" style="left:155px"><div class="ring"><svg width="50" height="40"><rect x="6" y="6" width="4" height="28" fill="#fff"/><circle cx="25" cy="20" r="12" fill="#fff"/><rect x="40" y="6" width="4" height="28" fill="#fff"/></svg></div><span>KITCHEN</span></div>
  <div class="abs service active" style="left:302px"><div class="ring"><svg width="50" height="40"><path d="M5 18h40v8a8 8 0 0 1-8 8H13a8 8 0 0 1-8-8z" fill="#fff"/></svg></div><span>BATH</span></div>
  <div class="abs service" style="left:450px"><div class="ring"><svg width="50" height="40"><rect x="6" y="20" width="38" height="5" fill="#fff"/><rect x="10" y="25" width="4" height="12" fill="#fff"/><rect x="36" y="25" width="4" height="12" fill="#fff"/><rect x="18" y="6" width="16" height="12" fill="#fff"/></svg></div><span>OFFICE</span></div>
  <div class="abs service" style="left:600px"><div class="ring"><svg width="50" height="44"><path d="M25 4l-8 8h16z M14 14h22l6 26H8z" fill="#fff"/></svg></div><span>CLOSET</span></div>
  <div class="abs service" style="left:747px"><div class="ring"><svg width="50" height="40"><rect x="4" y="22" width="42" height="5" fill="#fff"/><circle cx="25" cy="12" r="8" fill="#fff"/><rect x="8" y="27" width="4" height="10" fill="#fff"/><rect x="38" y="27" width="4" height="10" fill="#fff"/></svg></div><span>WORKSHOP</span></div>
  <div class="abs service" style="left:897px"><div class="ring"><svg width="50" height="40"><rect x="6" y="6" width="16" height="24" fill="#fff"/><rect x="28" y="16" width="16" height="14" fill="#fff"/><rect x="4" y="32" width="42" height="4" fill="#fff"/></svg></div><span>ENTERTAINMENT</span></div>
  <p class="abs">Each piece we build begins with a careful plan, fine timber and a steady hand. Our joiners shape cabinets, shelving and fixtures that suit the way you live, from busy family kitchens to quiet studies and bright bathrooms. We work with home owners and builders alike, guiding every project from first sketch to final fitting, so the finished room feels crafted, calm and made to last for many years to come.</p>
</section>

<h2 class="abs sec" style="left:160px;top:1212px">OUR GALLERY</h2>
<div class="abs thumb" style="left:160px;top:1255px;background:linear-gradient(135deg,#6a6a6a,#2e2e2e)" role="img" aria-label="Kitchen project photo"><div class="abs" style="left:76px;top:31px;width:40px;height:40px;border-radius:50%;background:var(--green)"></div></div>
<div class="abs thumb" style="left:363px;top:1255px" role="img" aria-label="Kitchen project photo"></div>
<div class="abs thumb" style="left:566px;top:1255px" role="img" aria-label="Kitchen project photo"></div>
<div class="abs thumb" style="left:160px;top:1372px" role="img" aria-label="Kitchen project photo"></div>
<div class="abs thumb" style="left:363px;top:1372px" role="img" aria-label="Kitchen project photo"></div>
<div class="abs thumb" style="left:566px;top:1372px" role="img" aria-label="Kitchen project photo"></div>
<div class="abs btn" style="left:160px;top:1488px;width:130px;background:#1e1e3a">VIEW MORE</div>

<h2 class="abs sec" style="left:786px;top:1212px">RECENT NEWS</h2>
<div class="abs news-item" style="top:1260px"><div class="pic" role="img" aria-label="News photo"></div><div><b>New oak finish range</b><span>A warm new oak stain now joins our list of cabinet finishes.</span></div></div>
<div class="abs news-item" style="top:1342px"><div class="pic" role="img" aria-label="News photo"></div><div><b>Showroom open days</b><span>Visit our workshop to see joinery being made by hand.</span></div></div>
<div class="abs news-item" style="top:1424px"><div class="pic" role="img" aria-label="News photo"></div><div><b>Builder partner plan</b><span>Trade pricing and support for builders of fine homes.</span></div></div>
<div class="abs btn" style="left:790px;top:1488px;width:128px;background:var(--green)">VIEW MORE</div>

<div class="abs rule"></div>

<h2 class="abs sec" style="left:160px;top:1603px">OUR CLIENTS</h2>
<div class="abs client" style="left:165px;top:1655px">Velora</div>
<div class="abs client" style="left:305px;top:1655px;font-size:30px">Casa Ferno</div>
<div class="abs client" style="left:483px;top:1655px">NORDA</div>
<div class="abs client" style="left:165px;top:1735px">NORDA</div>
<div class="abs client" style="left:305px;top:1735px">Kestrel</div>
<div class="abs client" style="left:465px;top:1735px;font-size:30px">Ashbury</div>

<h2 class="abs sec" style="left:627px;top:1603px">TESTIMONIALS</h2>
<div class="abs" style="left:627px;top:1652px;width:70px;height:70px;background:linear-gradient(#c9a58a,#6e4a36)" role="img" aria-label="Client portrait"></div>
<div class="abs quote">"Bramblewood built every cabinet in our new home. The fit is perfect, the finish is beautiful and the team kept us informed at each step. We could not be happier with the craft and care they brought to the work."</div>
<div class="abs" style="left:728px;top:1784px;font-size:13px;font-style:italic;color:#555">- Nora Vale</div>

<section class="abs hello">
  <h3 class="abs">HELLO !</h3>
  <p class="abs">We would love to hear about your next project. Tell us about the rooms you are planning and our team will help you choose the woods, finishes and fittings that suit your home.</p>
  <div class="abs circle" style="left:510px;top:155px;background:#2fa3e0"></div>
  <div class="abs circle" style="left:560px;top:155px;background:#3b5a9a"></div>
  <div class="abs circle" style="left:610px;top:155px;background:#d9402f"></div>
  <div class="abs circle" style="left:660px;top:155px;background:#1f7a44"></div>
</section>

<footer class="abs footer">
  <h4 class="abs" style="left:160px;top:95px">ABOUT US</h4>
  <p class="abs" style="left:160px;top:128px;width:260px;text-align:justify">Established in 1966, <b>Bramblewood Joinery</b> has long stood as one of the Midwest's most renowned makers of custom cabinets and fixtures. Our handcrafted, award-winning creations have been chosen by hundreds of noteworthy homebuilders. And while we custom build cabinets, we build our business around the belief that our customers absolutely, unequivocally come first.</p>
  <h4 class="abs" style="left:503px;top:95px">RECENT PORTFOLIO</h4>
  <div class="abs" style="left:503px;top:130px;display:grid;grid-template-columns:repeat(4,53px);gap:7px" role="img" aria-label="Portfolio photos of finished cabinetry">
    <div class="fthumb"></div><div class="fthumb"></div><div class="fthumb"></div><div class="fthumb"></div>
    <div class="fthumb"></div><div class="fthumb"></div><div class="fthumb"></div><div class="fthumb"></div>
    <div class="fthumb"></div><div class="fthumb"></div><div class="fthumb"></div><div class="fthumb"></div>
  </div>
  <h4 class="abs" style="left:789px;top:95px">CONTACT US</h4>
  <p class="abs" style="left:789px;top:128px;width:260px;font-size:11.5px;line-height:17px"><b>Got a question for Bramblewood? We'd love to hear from you! Whether it's for a project inquiry.</b><br><b>Bramblewood Joinery</b><br>Owen Harlow, 4410 Larkfield Road, Millbrook, ST-00421</p>
  <div class="abs" style="left:789px;top:225px;font-size:12.5px;color:#f3e8dc;line-height:26px">
    <div style="display:flex;gap:12px;align-items:center"><svg width="16" height="16"><circle cx="8" cy="8" r="7" fill="#fff"/><path d="M5 4l2 2-1 2 2 2 2-1 2 2-2 2c-4 0-7-3-7-7z" fill="#5a2a12"/></svg>555.014.2300</div>
    <div style="display:flex;gap:12px;align-items:center"><svg width="16" height="16"><rect x="1" y="3" width="14" height="11" rx="2" fill="#fff"/></svg>555.014.7835</div>
    <div style="display:flex;gap:12px;align-items:center"><svg width="16" height="16"><rect x="1" y="3" width="14" height="10" fill="#fff"/><path d="M1 3l7 6 7-6" stroke="#5a2a12" fill="none"/></svg>hello@bramblewoodjoinery.example</div>
  </div>
</footer>
<div class="abs bottom">
  <span class="abs" style="left:160px;top:10px">Home | Who Are We | Professional | Portfolio | Contact Us</span>
  <span class="abs" style="right:160px;top:10px">© 2015. All rights reserved. <b>Bramblewood Joinery.</b></span>
</div>

</body>
</html>
```